Business card design

I already have the logo design completed and am requiring business card design and layout utilising the logo. I require a front and back design.

We are an executive recruitment company so we are looking at full colour, high finish in a reasonably conservative structure.

Reason: will be provide ai template

Target Market(s)

Senior Management 35-60 age bracket

Industry/Entity Type

Business

Requirements
Must have
• Peter Welling
• Director
• 238 Morrow Tce, Kelvin Grove QLD 4059
• Ph: 07 3628 4190 Mob: 0418527306
• peter@voltinapartners.com.au
• www.voltinapartners.com.au
Nice to have
• Ideally full colour,
Should not have
• cheap looking

```html
<!DOCTYPE html>
<html lang="en">
<head>
<meta charset="utf-8">
<title>Voltina Partners – Business Card</title>
<link href="https://fonts.googleapis.com/css2?family=Open+Sans:wght@400;600;700&display=swap" rel="stylesheet">
<style>
  :root {
    --backdrop: #2a2a2c;
    --navy: #0f3a6b;
    --navy-deep: #0a2548;
    --navy-bright: #1c5b9c;
    --ink-grey: #6e6e6e;
    --soft-grey: #8a8a8a;
    --paper: #ffffff;
    --paper-shade: #ececec;
    --white: #ffffff;
  }
  * { margin: 0; padding: 0; box-sizing: border-box; }
  html, body {
    width: 1200px;
    height: 900px;
    overflow: hidden;
    background: var(--backdrop);
    font-family: "Open Sans", Arial, sans-serif;
  }
  .sheet {
    width: 1200px;
    height: 900px;
    display: flex;
    flex-direction: column;
    align-items: center;
    justify-content: center;
    gap: 40px;
  }
  .card {
    position: relative;
    width: 630px;
    height: 360px;
    overflow: hidden;
    box-shadow: 0 12px 30px rgba(0,0,0,0.45);
  }

  /* Back of card */
  .card-back {
    background: radial-gradient(ellipse at 35% 60%, var(--navy-bright) 0%, var(--navy) 45%, var(--navy-deep) 100%);
  }
  .card-back .brand {
    position: absolute;
    left: 170px;
    top: 140px;
    color: var(--white);
  }
  .card-back .website {
    position: absolute;
    right: 60px;
    top: 226px;
    color: var(--white);
    font-size: 15px;
    letter-spacing: 0.2px;
  }

  /* Brand lockup */
  .brand {
    display: flex;
    align-items: center;
    gap: 14px;
  }
  .brand-dot {
    width: 40px;
    height: 40px;
    border-radius: 50%;
    background: currentColor;
    flex: none;
  }
  .brand-name {
    font-size: 30px;
    font-weight: 700;
    letter-spacing: 1.5px;
    text-transform: uppercase;
    white-space: nowrap;
  }

  /* Front of card */
  .card-front {
    background: linear-gradient(160deg, var(--paper) 0%, var(--paper) 55%, var(--paper-shade) 100%);
  }
  .card-front::after {
    content: "";
    position: absolute;
    top: 0;
    right: 0;
    width: 12px;
    height: 100%;
    background: var(--navy);
  }
  .card-front .brand {
    position: absolute;
    left: 50px;
    top: 78px;
    color: var(--navy);
  }
  .holder {
    position: absolute;
    left: 50px;
    top: 218px;
  }
  .holder-name {
    font-size: 22px;
    font-weight: 700;
    color: var(--navy);
    line-height: 1.2;
  }
  .holder-title {
    font-size: 19px;
    color: var(--ink-grey);
    letter-spacing: 0.5px;
  }
  .contact {
    position: absolute;
    left: 338px;
    top: 128px;
    list-style: none;
    font-size: 15px;
    line-height: 1.6;
    color: var(--soft-grey);
    letter-spacing: 0.4px;
  }
  .contact .email { font-size: 14px; letter-spacing: 0; }
</style>
</head>
<body>
  <main class="sheet">
    <section class="card card-back" aria-label="Card back">
      <div class="brand">
        <span class="brand-dot" aria-hidden="true"></span>
        <span class="brand-name">Voltina Partners</span>
      </div>
      <p class="website">www.voltinapartners.com.au</p>
    </section>

    <section class="card card-front" aria-label="Card front">
      <div class="brand">
        <span class="brand-dot" aria-hidden="true"></span>
        <span class="brand-name">Voltina Partners</span>
      </div>
      <div class="holder">
        <p class="holder-name">Peter Welling</p>
        <p class="holder-title">Director</p>
      </div>
      <ul class="contact">
        <li>238 Morrow Tce, Kelvin Grove</li>
        <li>QLD 4059</li>
        <li>P: 07 3628 4190</li>
        <li>M: 0418 527 306</li>
        <li class="email">peter@voltinapartners.com.au</li>
      </ul>
    </section>
  </main>
</body>
</html>
```